business card

Business card for new business.
Red and black corporate colors.
Card can have an Indsutrial feel to it. Feel free to add Rust, Bolted steel, or graphics as you see fit. We provide highly specialized services to the below mentioned industries.
Keep information out of corners so that if I want I can choose rounded corners.
Information
- front. name - title - phone - email
- Rear
Forestry - Power - Pipelines - Marine - Utilities
Northbrook - Ashford - Port Kelso - Granite Falls - Westhaven

```html
<!DOCTYPE html>
<html lang="en">
<head>
<meta charset="utf-8">
<title>Ironvale business card</title>
<link rel="stylesheet" href="https://fonts.googleapis.com/css2?family=Roboto:wght@400;700&display=swap">
<style>
  :root {
    --backdrop: #222222;
    --steel-light: #f1f1f1;
    --steel-mid: #d9d9d9;
    --steel-dark: #c4c4c4;
    --brand-red: #e3101c;
    --ink: #4a4a4a;
    --ink-soft: #7a7a7a;
    --logo-grey: #7b7b7b;
  }
  html, body {
    margin: 0;
    width: 1200px;
    height: 960px;
    overflow: hidden;
    background: var(--backdrop);
    font-family: "Roboto", Arial, sans-serif;
  }
  .card {
    position: absolute;
    width: 600px;
    height: 343px;
    background:
      repeating-linear-gradient(90deg, rgba(255,255,255,0.35) 0 1px, rgba(0,0,0,0.04) 1px 3px, rgba(255,255,255,0.15) 3px 5px),
      linear-gradient(180deg, var(--steel-mid) 0%, var(--steel-light) 45%, var(--steel-light) 60%, var(--steel-dark) 100%);
    box-shadow: 0 4px 10px rgba(0,0,0,0.6);
    text-align: center;
    color: var(--ink);
  }
  .card--front { left: 314px; top: 113px; }
  .card--back { left: 311px; top: 472px; }

  .front-frame {
    position: absolute;
    left: 15px; top: 13px; right: 15px; bottom: 15px;
    border: 2px solid var(--brand-red);
  }
  .holder-name {
    position: absolute;
    top: 120px; left: 0; right: 0;
    font-weight: 700;
    font-size: 22px;
    color: var(--brand-red);
    letter-spacing: 0.3px;
  }
  .holder-title {
    position: absolute;
    top: 147px; left: 0; right: 0;
    font-size: 15px;
    color: var(--ink-soft);
  }
  .divider {
    position: absolute;
    top: 172px; left: 175px;
    width: 250px; height: 1px;
    background: linear-gradient(90deg, transparent, rgba(227,16,28,0.45), transparent);
  }
  .contact-line {
    position: absolute;
    top: 185px; left: 0; right: 0;
    font-size: 15px;
  }
  .web-line {
    position: absolute;
    top: 204px; left: 0; right: 0;
    font-size: 15px;
    letter-spacing: 1.6px;
  }

  .brand-mark {
    position: absolute;
    top: 140px; left: 0; right: 0;
    display: flex;
    justify-content: center;
    align-items: center;
    gap: 14px;
  }
  .brand-square {
    width: 26px; height: 26px;
    background: var(--brand-red);
  }
  .brand-name {
    font-weight: 700;
    font-size: 56px;
    line-height: 1;
    color: var(--logo-grey);
    letter-spacing: 1px;
  }
  .sectors {
    position: absolute;
    top: 256px; left: 0; right: 0;
    font-size: 15px;
    line-height: 18px;
    color: var(--ink);
  }
  .dot { color: var(--brand-red); font-size: 12px; }
</style>
</head>
<body>
  <section class="card card--front">
    <div class="front-frame"></div>
    <div class="holder-name">DALE MORROW</div>
    <div class="holder-title">CEO/FOUNDER</div>
    <div class="divider"></div>
    <div class="contact-line">P. 555 010 4471 E . info@ironvale.com</div>
    <div class="web-line">www.ironvale.com</div>
  </section>

  <section class="card card--back">
    <div class="brand-mark">
      <span class="brand-square"></span>
      <span class="brand-name">IRONVALE</span>
    </div>
    <div class="sectors">
      Forestry <span class="dot">●</span> Power <span class="dot">●</span> Pipelines <span class="dot">●</span> Marine<br>
      Utilities <span class="dot">●</span> Northbrook <span class="dot">●</span> Ashford <span class="dot">●</span> Port Kelso<br>
      Granite Falls <span class="dot">●</span> Westhaven
    </div>
  </section>
</body>
</html>
```